Form Sculptors Business Card

Professional cosmetic surgery company, based in very exclusive area in London. High profiled clientele. Brand is very artistic, modern, state-of-the-art, safe. The best in the business. Celebrity clientele.

Form Sculptor’s of London is a brand serving a discriminating and exclusive clientele who value personal service that is both intimate and high end. Our clients choose Form Sculptors because of the relationships we share with all of our customers. The clients of Form Sculptors have an equal partnership between customers, and very experienced, highly qualified medical professionals. This together provides you with a professional service that keeps you looking good and feeling good. It is a relationship based on honesty, compassion, loyalty and respect.
Form Sculptor’s have provided services for internationally recognised celebrities, and other high profiled individuals.

The cards are used for networking at private, exclusive events with VIPs.

Target Market(s)

Professionals
Rich people

Industry/Entity Type

Professional Service

Contact Information for Business Card

Need double sided business card design for 4 people. Back of the business card needs to have contrast background to the front with butterfly watermark with services provided:
Hair Restoration surgery
Hair Loss treatments
Breast surgery
Rhinoplasty
Pulvix Liposuction
Fat Grafting
Lumaxin & Fillers

Front of the business card needs to be a nice satin black.
with following information:
Calvert Osterlund - name
Chief Executive - Job title

www.formsculptors-example.co.uk
calvert@formsculptors-example.co.uk
Phone: +44 (0)207 946 0321
Mobile: +44 (0)7700 900 147

The London Farrowmere Clinic
14 Farrowmere Lane | London | W1X 4QP
Off Quenby Street

All business cards have the same address, phone, website as Calvert's details.
Same details on the back of the business card as well.
The other cards have different name, job title, email, mobile number

Teodor Lunn - Name
Partner - Job Title
Former England International Cricketer - please include below job title

email: teodor@formsculptors-example.co.uk
mobile: +44(0)7700 900582

Dr Castello Vranesk - Name
Plastic Surgeon - Job Title
drvranesk@formsculptors-example.co.uk
No mobile number

Dr Ezra Tolquist FRCS (please put FRCS in small font) - Name
Hair Restoration Surgeon - Job Title
drtolquist@formsculptors-example.co.uk
No mobile number

Colors
cedeec
85abd2
0655a3

Requirements
Must have
• The logo needs to be in a metallic finish
• Text needs to be striking
• nice background
• butterfly watermark on the back

```html
<!DOCTYPE html>
<html lang="en">
<head>
<meta charset="utf-8">
<title>Form Sculptors – Business Card</title>
<link rel="stylesheet" href="https://fonts.googleapis.com/css2?family=Lato:wght@400;700&display=swap">
<style>
  :root {
    --page: #eceef1;
    --satin-dark: #1c1d21;
    --satin-light: #2e3035;
    --brand-blue: #1b82c4;
    --band-blue: #2a8fd0;
    --accent-blue: #2a8fd0;
    --pale-blue: #cedeec;
    --light-ink: #e9ecef;
    --muted-ink: #b9bec5;
    --rule-dark: #4a4d54;
    --watermark: rgba(255, 255, 255, 0.2);
  }
  * { box-sizing: border-box; margin: 0; padding: 0; }
  html, body { width: 1000px; height: 1200px; overflow: hidden; }
  body {
    background: var(--page);
    font-family: "Lato", Arial, sans-serif;
    color: var(--light-ink);
    position: relative;
  }
  .card {
    position: absolute;
    left: 60px;
    width: 880px;
    height: 520px;
    overflow: hidden;
  }
  .card--front {
    top: 60px;
    background: linear-gradient(135deg, var(--satin-light) 0%, var(--satin-dark) 55%, var(--satin-light) 100%);
  }
  .card--back { top: 620px; background: var(--brand-blue); }

  /* Front */
  .brand-band {
    position: absolute; left: 67px; top: 57px; width: 746px; height: 161px;
    background: var(--band-blue);
    display: flex; align-items: center; justify-content: center; gap: 14px;
  }
  .brand-mark { width: 34px; height: 34px; border-radius: 50%; background: var(--pale-blue); }
  .brand-name { font-size: 44px; font-weight: 400; color: var(--pale-blue); letter-spacing: 1px; }
  .rule { position: absolute; height: 1px; background: var(--rule-dark); }
  .rule--top { left: 67px; width: 746px; top: 234px; }
  .rule--bottom { left: 67px; width: 746px; top: 460px; }
  .rule--divider { left: 446px; top: 288px; width: 1px; height: 151px; }

  .contact-list { position: absolute; left: 67px; top: 258px; list-style: none; }
  .contact-item {
    display: flex; align-items: center; gap: 12px;
    height: 26px; margin-bottom: 24.5px;
    font-size: 17px; color: var(--light-ink);
    white-space: nowrap;
  }
  .contact-icon { width: 34px; height: 34px; flex: none; }

  .person { position: absolute; left: 446px; width: 434px; top: 318px; text-align: center; padding-right: 67px; }
  .person-name { font-size: 33px; font-weight: 400; letter-spacing: 0.5px; white-space: nowrap; color: #ffffff; }
  .person-name .given { font-weight: 700; color: var(--accent-blue); }
  .person-role { font-size: 15px; letter-spacing: 0.5px; margin-top: 2px; color: var(--muted-ink); }

  /* Back */
  .watermark { position: absolute; left: 330px; top: 22px; width: 220px; height: 220px; }
  .back-rule { position: absolute; left: 57px; width: 766px; height: 2px; background: #ffffff; opacity: 0.9; }
  .back-rule--top { top: 252px; }
  .back-rule--bottom { top: 337px; }
  .back-title {
    position: absolute; left: 0; width: 100%; top: 264px; text-align: center;
    color: #ffffff; font-size: 35px; letter-spacing: 0.5px;
  }
  .back-title strong { font-weight: 700; }
  .back-url {
    position: absolute; left: 0; width: 100%; top: 306px; text-align: center;
    color: #ffffff; font-size: 19px; font-weight: 700; letter-spacing: 1px;
  }
  .services {
    position: absolute; left: 57px; width: 766px; top: 356px;
    text-align: center; color: #ffffff; font-size: 17px; line-height: 28px;
  }
  .services span + span::before { content: "|"; margin: 0 10px; opacity: 0.7; }
  .back-contact {
    position: absolute; left: 57px; width: 766px; top: 430px;
    text-align: center; color: var(--pale-blue); font-size: 15px; line-height: 24px;
  }
  .back-contact span + span::before { content: "|"; margin: 0 8px; opacity: 0.7; }
</style>
</head>
<body>

<section class="card card--front" aria-label="Business card front">
  <div class="brand-band">
    <span class="brand-mark"></span>
    <span class="brand-name">Form Sculptors</span>
  </div>
  <div class="rule rule--top"></div>

  <ul class="contact-list">
    <li class="contact-item">
      <svg class="contact-icon" viewBox="0 0 34 34" aria-hidden="true">
        <circle cx="17" cy="17" r="17" fill="#2a8fd0"/>
        <path d="M9 17.5 17 10l8 7.5h-2.5V25h-4v-5h-3v5h-4v-7.5z" fill="#fff"/>
      </svg>
      The London Farrowmere Clinic 14 Farrowmere Lane
    </li>
    <li class="contact-item">
      <svg class="contact-icon" viewBox="0 0 34 34" aria-hidden="true">
        <circle cx="17" cy="17" r="17" fill="#2a8fd0"/>
        <path d="M9 14c0-2 2-3.5 8-3.5s8 1.5 8 3.5v1.5h-4V13.5h-8V15.5H9z" fill="#fff"/>
        <rect x="11" y="17" width="12" height="7" rx="1.5" fill="#fff"/>
      </svg>
      +44 (0)207 946 0321
    </li>
    <li class="contact-item">
      <svg class="contact-icon" viewBox="0 0 34 34" aria-hidden="true">
        <circle cx="17" cy="17" r="17" fill="#2a8fd0"/>
        <rect x="9" y="11.5" width="16" height="11" rx="1" fill="#fff"/>
        <path d="M9.5 12 17 18l7.5-6" fill="none" stroke="#2a8fd0" stroke-width="1.5"/>
      </svg>
      calvert@formsculptors-example.co.uk
    </li>
    <li class="contact-item">
      <svg class="contact-icon" viewBox="0 0 34 34" aria-hidden="true">
        <circle cx="17" cy="17" r="17" fill="#2a8fd0"/>
        <g fill="none" stroke="#fff" stroke-width="2.2" stroke-linecap="round">
          <path d="M15 19l-2.5 2.5a2.5 2.5 0 0 1-3.5-3.5L12 15"/>
          <path d="M19 15l2.5-2.5a2.5 2.5 0 0 1 3.5 3.5L22 19"/>
          <path d="M14 20l6-6"/>
        </g>
      </svg>
      www.formsculptors-example.co.uk
    </li>
  </ul>

  <div class="rule rule--divider"></div>

  <div class="person">
    <p class="person-name"><span class="given">CALVERT</span> OSTERLUND</p>
    <p class="person-role">CHIEF EXECUTIVE</p>
  </div>

  <div class="rule rule--bottom"></div>
</section>

<section class="card card--back" aria-label="Business card back">
  <svg class="watermark" viewBox="0 0 220 220" role="img" aria-label="Faint brand watermark area">
    <circle cx="110" cy="110" r="108" fill="var(--watermark)"/>
  </svg>
  <div class="back-rule back-rule--top"></div>
  <p class="back-title"><strong>FORMSCULPTORS</strong> COMPANY</p>
  <p class="back-url">WWW.FORMSCULPTORS-EXAMPLE.CO.UK</p>
  <div class="back-rule back-rule--bottom"></div>

  <div class="services" aria-label="Services">
    <p><span>Hair Restoration Surgery</span><span>Hair Loss Treatments</span><span>Breast Surgery</span><span>Rhinoplasty</span></p>
    <p><span>Pulvix Liposuction</span><span>Fat Grafting</span><span>Lumaxin &amp; Fillers</span></p>
  </div>

  <div class="back-contact">
    <p><span>Phone: +44 (0)207 946 0321</span><span>Mobile: +44 (0)7700 900 147</span></p>
    <p><span>The London Farrowmere Clinic</span><span>14 Farrowmere Lane</span><span>London</span><span>W1X 4QP</span></p>
  </div>
</section>

</body>
</html>
```